Business card

We need a business card design for our company based in Auckland , New Zealand called 'Ridge + Studio Ltd'. We provide architectural services. We would like to see designs that use the max. three colours (such as white, black, grey) The final design should communicate financial safety and growth."
Also I will provide our company logo. I would like to the logo to be embeded onto our business card.

Target Market(s)

new residential house, alteration & addition & light commericila design & drafting service

Industry/Entity Type

Architecture

Contact Information for Business Card

Company name: ridge + studio Ltd.
Name: Mark Delford
Job title: architectural designer & Design LBP
email address: mark@rplusd.co.nz
mobile number: 02 5163 2290
web site: www.rplusd.co.nz

Requirements
Must have
• My project must have..
• - embeded logo (attached company logo)
• I don't have a bigger version for our company logo, but I have one old one, so you can remove the word from it)
• - insert the attached small BKTW logo & LBP logo
• - creative, simple and clear business card.
• - Max. three colours
Nice to have
• - Here are the samples I would like to share with you: http://www.plimvora.com/blog/minimalistic-business-card-designs/
• I would like to have my business card like one of the creation.
Should not have
• TBA

```html
<!DOCTYPE html>
<html lang="en">
<head>
<meta charset="utf-8">
<title>Ridge + Studio Ltd. — Business Card</title>
<link href="https://fonts.googleapis.com/css2?family=Nunito+Sans:wght@400;600;700&display=swap" rel="stylesheet">
<style>
  :root {
    --page: #ffffff;
    --card: #d3d3d3;
    --ink: #333333;
    --ink-soft: #3c3c3c;
    --rule: #f2f2f2;
    --badge: #ffffff;
    --badge-ring: #2f2f2f;
    --member: #555a58;
  }
  html, body {
    margin: 0;
    padding: 0;
    width: 1200px;
    height: 1192px;
    overflow: hidden;
    background: var(--page);
    font-family: "Nunito Sans", sans-serif;
    color: var(--ink);
  }
  .card {
    position: absolute;
    left: 262px;
    width: 676px;
    height: 396px;
    background: var(--card);
    border-radius: 14px;
  }
  .card--front { top: 144px; }
  .card--back { top: 620px; }

  .brand-mark {
    position: absolute;
    left: 270px;
    top: 94px;
    width: 136px;
    height: 136px;
  }
  .company-name {
    position: absolute;
    left: 0;
    right: 0;
    top: 262px;
    margin: 0;
    text-align: center;
    font-size: 29px;
    font-weight: 700;
    letter-spacing: -0.4px;
    color: var(--ink);
  }

  .lbp-badge {
    position: absolute;
    left: 68px;
    top: 224px;
    width: 104px;
    height: 104px;
  }
  .member-mark {
    position: absolute;
    left: 202px;
    top: 238px;
    margin: 0;
    font-size: 26px;
    font-weight: 700;
    letter-spacing: -0.5px;
    color: var(--member);
  }

  .person {
    position: absolute;
    left: 408px;
    top: 136px;
  }
  .person-name {
    margin: 0;
    font-size: 17px;
    font-weight: 700;
    color: var(--ink);
  }
  .person-title {
    margin: 6px 0 0;
    font-size: 12.5px;
    font-weight: 400;
    color: var(--ink-soft);
  }
  .divider {
    position: absolute;
    left: 408px;
    top: 209px;
    width: 212px;
    height: 1px;
    background: var(--rule);
  }
  .contact-list {
    position: absolute;
    left: 384px;
    top: 226px;
    margin: 0;
    padding: 0;
    list-style: none;
  }
  .contact-item {
    display: flex;
    align-items: center;
    height: 32px;
    font-size: 17px;
    color: var(--ink-soft);
  }
  .contact-icon {
    width: 16px;
    height: 16px;
    margin-right: 8px;
    flex: none;
  }
</style>
</head>
<body>

<section class="card card--front">
  <svg class="brand-mark" viewBox="0 0 136 136" role="img" aria-label="Company logo mark">
    <circle cx="68" cy="68" r="62" fill="none" stroke="var(--ink)" stroke-width="8"/>
  </svg>
  <h1 class="company-name">Ridge + Studio Ltd.</h1>
</section>

<section class="card card--back">
  <svg class="lbp-badge" viewBox="0 0 104 104" role="img" aria-label="Licensed building practitioner badge">
    <circle cx="52" cy="52" r="50" fill="var(--badge)"/>
    <circle cx="52" cy="52" r="46" fill="none" stroke="var(--badge-ring)" stroke-width="9"/>
  </svg>
  <p class="member-mark">BKTW</p>

  <div class="person">
    <p class="person-name">Mark Delford</p>
    <p class="person-title">architectural designer &amp; Design LBP</p>
  </div>
  <div class="divider"></div>

  <ul class="contact-list">
    <li class="contact-item">
      <svg class="contact-icon" viewBox="0 0 16 16" aria-hidden="true">
        <circle cx="8" cy="8" r="7" fill="none" stroke="var(--ink)" stroke-width="1.3"/>
        <path d="M6 4.5 Q9 8 6 11.5" fill="none" stroke="var(--ink)" stroke-width="1.6" stroke-linecap="round"/>
      </svg>
      <span>02 5163 2290</span>
    </li>
    <li class="contact-item">
      <svg class="contact-icon" viewBox="0 0 16 16" aria-hidden="true">
        <rect x="1" y="3" width="14" height="10" fill="var(--ink)"/>
        <path d="M1.5 3.5 L8 9 L14.5 3.5 M1.5 12.5 L6 8 M14.5 12.5 L10 8" fill="none" stroke="var(--card)" stroke-width="1.1"/>
      </svg>
      <span>mark@rplusd.co.nz</span>
    </li>
    <li class="contact-item">
      <svg class="contact-icon" viewBox="0 0 16 16" aria-hidden="true">
        <circle cx="8" cy="8" r="7" fill="none" stroke="var(--ink)" stroke-width="1.3"/>
        <ellipse cx="8" cy="8" rx="3" ry="7" fill="none" stroke="var(--ink)" stroke-width="1.1"/>
        <path d="M1 8 H15 M2.5 4.5 H13.5 M2.5 11.5 H13.5" stroke="var(--ink)" stroke-width="1.1"/>
      </svg>
      <span>www.rplusd.co.nz</span>
    </li>
  </ul>
</section>

</body>
</html>
```